Company director needs a business card design

I am a semi-retired former senior finance executive who sits on a number of public and private company boards and do some consulting work. I work largely with emerging businesses but deal regularly with top end of town lawyers, bankers etc. I need a thoughtful but relatively conservative design which would also resonate with my younger client base. Some colour would be good. Information limited to name, address, office tel, mobile and email.

Finance

```html
<!DOCTYPE html>
<html lang="en">
<head>
<meta charset="utf-8">
<title>Business Card – Rowan</title>
<link href="https://fonts.googleapis.com/css2?family=Open+Sans:wght@400;700&display=swap" rel="stylesheet">
<style>
  :root {
    --backdrop: #d9dadc;
    --card: #262627;
    --accent: #1ea9e6;
    --accent-soft: rgba(30, 169, 230, 0.55);
    --ink-light: #ffffff;
  }
  * { margin: 0; padding: 0; box-sizing: border-box; }
  html, body {
    width: 1200px;
    height: 800px;
    overflow: hidden;
    background: var(--backdrop);
    font-family: "Open Sans", Arial, sans-serif;
  }
  .business-card {
    position: absolute;
    left: 75px;
    top: 100px;
    width: 1050px;
    height: 600px;
    background: var(--card);
    overflow: hidden;
  }
  .accent-artwork {
    position: absolute;
    left: 610px;
    top: 0;
    width: 440px;
    height: 390px;
    background: radial-gradient(ellipse at 60% 35%, var(--accent-soft) 0%, rgba(30, 169, 230, 0.25) 45%, rgba(38, 38, 39, 0) 75%);
  }
  .identity {
    position: absolute;
    left: 200px;
    top: 232px;
  }
  .identity__name {
    color: var(--ink-light);
    font-weight: 700;
    font-size: 36px;
    line-height: 1.1;
  }
  .identity__role {
    color: var(--accent);
    font-weight: 400;
    font-size: 24px;
    line-height: 1.1;
    margin-left: 20px;
  }
  .contact-list {
    position: absolute;
    left: 240px;
    top: 318px;
    list-style: none;
  }
  .contact-list__item {
    display: flex;
    align-items: center;
    height: 50px;
    color: var(--accent);
    font-size: 24px;
    white-space: nowrap;
  }
  .contact-list__icon {
    width: 26px;
    height: 26px;
    margin-right: 36px;
    fill: var(--ink-light);
    flex: none;
  }
</style>
</head>
<body>
  <div class="business-card">
    <div class="accent-artwork" role="img" aria-label="Brushed blue circular accent artwork"></div>

    <div class="identity">
      <div class="identity__name">Rowan</div>
      <div class="identity__role">manager</div>
    </div>

    <ul class="contact-list">
      <li class="contact-list__item">
        <svg class="contact-list__icon" viewBox="0 0 24 24" aria-label="Office phone">
          <path d="M6.6 10.8a15.1 15.1 0 0 0 6.6 6.6l2.2-2.2c.3-.3.7-.4 1-.2 1.1.4 2.3.6 3.6.6.6 0 1 .4 1 1V20c0 .6-.4 1-1 1A17 17 0 0 1 3 4c0-.6.4-1 1-1h3.5c.6 0 1 .4 1 1 0 1.3.2 2.5.6 3.6.1.3 0 .7-.2 1z"/>
        </svg>
        <span>4127-3590</span>
      </li>
      <li class="contact-list__item">
        <svg class="contact-list__icon" viewBox="0 0 24 24" aria-label="Mobile">
          <path d="M7 1h10a2 2 0 0 1 2 2v18a2 2 0 0 1-2 2H7a2 2 0 0 1-2-2V3a2 2 0 0 1 2-2zm0 3v14h10V4zm5 15.5a1.2 1.2 0 1 0 0 2.4 1.2 1.2 0 0 0 0-2.4z"/>
        </svg>
        <span>00 482 615 307</span>
      </li>
      <li class="contact-list__item">
        <svg class="contact-list__icon" viewBox="0 0 24 24" aria-label="Address">
          <path d="M12 2a7 7 0 0 0-7 7c0 5.2 7 13 7 13s7-7.8 7-13a7 7 0 0 0-7-7zm0 9.5a2.5 2.5 0 1 1 0-5 2.5 2.5 0 0 1 0 5z"/>
        </svg>
        <span>214 Harrow Lane, BC</span>
      </li>
      <li class="contact-list__item">
        <svg class="contact-list__icon" viewBox="0 0 24 24" aria-label="Email">
          <path d="M2 5h20v2l-10 6L2 7zm0 4.3 10 6 10-6V19H2z"/>
        </svg>
        <span>email-rowan214@mailbox.com</span>
      </li>
    </ul>
  </div>
</body>
</html>
```